CopperWanderer Stretching and Strength

We need a application design for a our first IOS application. the goal of the application is to categorize stretching and strength routines for triathlon.

We would like to see designs that use the color orange.

The design of the application should be compliant with the last version of the IOS Mobile.

For this first design we need the folowing pages:

1- Sign up
2- Log in
3- Home
4- View Exercises
5- Do it
6- Profile

The description of each page is in the attached document.

We need a logo design for the application. The logo should express that mission of the application that is for stretch and strength training for Triathlon.

We will use https://pellavokit.example to develop the application, if you have any experience of the limitation that this technology have it will be a plus.

If you have any question please feel free to contact us.

Reason: We will extend the deadline to be sure that we select the best design from all of you. we will take the final decision next Tuesday.

Target Market(s)

The market for my aplicación is the Running a Triathlon world.

Logo Text

CopperWanderer

Font styles to use
Serif

Colors
f37122
ffffff
dcdcdc

Requirements
Must have
• In some future we will add more features in the menu. We should considere it for the design.
• The designs should include all the screens in the power point.

```html
<!DOCTYPE html>
<html lang="en">
<head>
<meta charset="utf-8">
<title>Do It – Exercise Detail</title>
<link rel="stylesheet" href="https://fonts.googleapis.com/css2?family=Roboto:wght@400;500&display=swap">
<style>
  :root {
    --orange: #f37130;
    --orange-light: #f9a070;
    --backdrop: #d6e3ef;
    --screen-bg: #e9eef1;
    --white: #ffffff;
    --text-dark: #2b2b2b;
    --text-body: #5c5c5c;
    --text-muted: #7a7a7a;
    --track: #e8ecef;
    --tag-cyan: #22b7d9;
    --tag-violet: #b96fd6;
    --tag-indigo: #6a5ae6;
  }
  * { box-sizing: border-box; margin: 0; padding: 0; }
  html, body { width: 1200px; height: 1200px; overflow: hidden; }
  body {
    background: var(--backdrop);
    font-family: "Roboto", Arial, sans-serif;
    position: relative;
  }
  .screen {
    position: absolute;
    left: 275px; top: 20px;
    width: 650px; height: 1160px;
    background: var(--screen-bg);
    overflow: hidden;
  }
  .app-bar {
    position: absolute; left: 0; top: 0; width: 100%; height: 117px;
    background: var(--orange); color: var(--white);
  }
  .status-bar {
    position: absolute; left: 0; top: 0; width: 100%; height: 50px;
    font-size: 19px; display: flex; align-items: center; padding: 0 10px;
  }
  .status-left { display: flex; align-items: center; gap: 6px; flex: 1; }
  .status-time { position: absolute; left: 0; right: 0; text-align: center; }
  .status-right { display: flex; align-items: center; gap: 8px; }
  .title-row { position: absolute; top: 62px; left: 0; width: 100%; height: 44px; }
  .back-arrow { position: absolute; left: 14px; top: 8px; }
  .page-title {
    text-align: center; font-size: 26px; font-weight: 500; line-height: 44px; letter-spacing: .5px;
  }
  .media-toggle {
    position: absolute; left: 126px; top: 135px; width: 397px; height: 50px;
    background: var(--white); border-radius: 25px; display: flex; overflow: hidden;
    box-shadow: 0 1px 3px rgba(0,0,0,.08);
  }
  .toggle-option {
    flex: 1; display: flex; align-items: center; justify-content: center; gap: 12px;
    font-size: 22px; color: var(--orange);
  }
  .toggle-option.is-active { background: var(--orange); color: var(--white); border-radius: 25px; }
  .card {
    position: absolute; left: 15px; width: 619px; background: var(--white);
    box-shadow: 0 1px 3px rgba(0,0,0,.1);
  }
  .exercise-card { top: 209px; height: 696px; }
  .video-frame {
    position: absolute; left: 11px; top: 10px; width: 597px; height: 330px;
    background: linear-gradient(180deg, #e6c79c 0%, #c9b48f 45%, #6f8a45 70%, #4f6b2c 100%);
  }
  .play-icon { position: absolute; left: 50%; top: 50%; transform: translate(-50%, -50%); }
  .exercise-title {
    position: absolute; left: 12px; top: 360px; font-size: 26px; color: var(--text-dark); font-weight: 400;
  }
  .tags { position: absolute; left: 12px; top: 405px; display: flex; gap: 8px; }
  .tag {
    height: 18px; padding: 0 14px; border-radius: 9px; font-size: 11px; line-height: 18px;
    color: var(--white); font-weight: 500;
  }
  .tag-flexibility { background: var(--tag-cyan); }
  .tag-leg { background: var(--tag-violet); }
  .tag-pain { background: var(--tag-indigo); }
  .exercise-description {
    position: absolute; left: 12px; top: 441px; width: 600px;
    font-size: 20px; line-height: 26px; color: var(--text-body);
  }
  .meta { position: absolute; left: 12px; font-size: 20px; color: var(--text-body); }
  .meta-label { color: var(--orange); }
  .meta-time { top: 617px; }
  .meta-level { top: 653px; }
  .timer-card { top: 917px; height: 124px; }
  .timer-label { position: absolute; left: 12px; top: 14px; font-size: 20px; color: var(--text-dark); }
  .timer-note { position: absolute; right: 15px; top: 30px; font-size: 15px; color: var(--text-muted); }
  .progress-track {
    position: absolute; left: 12px; top: 54px; width: 592px; height: 52px;
    background: var(--track); border: 1px solid #d9dfe3;
  }
  .progress-fill {
    height: 100%; width: 33%;
    background: linear-gradient(90deg, var(--orange) 0%, var(--orange-light) 100%);
    color: var(--white); font-size: 18px; line-height: 50px; text-align: center;
  }
  .start-button {
    position: absolute; left: 44px; top: 1070px; width: 561px; height: 71px;
    background: var(--orange); border-radius: 36px; color: var(--white);
    font-size: 26px; font-weight: 500; text-align: center; line-height: 71px;
    box-shadow: 0 4px 8px rgba(243,113,48,.3); letter-spacing: .5px;
  }
</style>
</head>
<body>
<main class="screen">
  <header class="app-bar">
    <div class="status-bar">
      <div class="status-left">
        <svg width="62" height="12" viewBox="0 0 62 12" aria-hidden="true">
          <circle cx="6" cy="6" r="5" fill="#fff"/><circle cx="18" cy="6" r="5" fill="#fff"/><circle cx="30" cy="6" r="5" fill="#fff"/>
          <circle cx="42" cy="6" r="4.4" fill="none" stroke="#fff" stroke-width="1.2"/><circle cx="54" cy="6" r="4.4" fill="none" stroke="#fff" stroke-width="1.2"/>
        </svg>
        <span>NORTHLINE</span>
        <svg width="22" height="16" viewBox="0 0 22 16" aria-hidden="true">
          <path d="M1 5a14 14 0 0 1 20 0" fill="none" stroke="#fff" stroke-width="2.2"/>
          <path d="M4.5 8.5a9 9 0 0 1 13 0" fill="none" stroke="#fff" stroke-width="2.2"/>
          <path d="M11 15l-3-3a4.5 4.5 0 0 1 6 0z" fill="#fff"/>
        </svg>
      </div>
      <span class="status-time">4:21 PM</span>
      <div class="status-right">
        <svg width="12" height="20" viewBox="0 0 12 20" aria-hidden="true">
          <path d="M1 5l10 9-5 5V1l5 5-10 9" fill="none" stroke="#fbc9ad" stroke-width="1.6"/>
        </svg>
        <span>100%</span>
        <svg width="42" height="18" viewBox="0 0 42 18" aria-hidden="true">
          <rect x="1" y="1" width="36" height="16" rx="3" fill="none" stroke="#fff" stroke-width="1.5"/>
          <rect x="3" y="3" width="32" height="12" rx="1.5" fill="#fff"/>
          <rect x="38.5" y="6" width="2.5" height="6" rx="1" fill="#fff"/>
        </svg>
      </div>
    </div>
    <div class="title-row">
      <svg class="back-arrow" width="32" height="26" viewBox="0 0 32 26" aria-label="Back">
        <path d="M30 13H3M13 3L3 13l10 10" fill="none" stroke="#fff" stroke-width="2.4" stroke-linecap="round" stroke-linejoin="round"/>
      </svg>
      <h1 class="page-title">DO IT</h1>
    </div>
  </header>

  <nav class="media-toggle">
    <div class="toggle-option">
      <svg width="26" height="20" viewBox="0 0 26 20" aria-hidden="true">
        <rect x="1.5" y="1.5" width="23" height="17" fill="none" stroke="var(--orange)" stroke-width="2.4"/>
        <path d="M3 17l7-8 5 5 3-3 5 6z" fill="var(--orange)"/><circle cx="18" cy="6.5" r="2" fill="var(--orange)"/>
      </svg>
      <span>Image</span>
    </div>
    <div class="toggle-option is-active">
      <svg width="28" height="20" viewBox="0 0 28 20" aria-hidden="true">
        <rect x="0" y="0" width="28" height="20" rx="4" fill="#fff"/><path d="M11 5l8 5-8 5z" fill="var(--orange)"/>
      </svg>
      <span>Video</span>
    </div>
  </nav>

  <section class="card exercise-card">
    <div class="video-frame" role="img" aria-label="Video preview: a group of older adults practising slow standing stretches outdoors on a grassy park lawn">
      <svg class="play-icon" width="76" height="76" viewBox="0 0 76 76" aria-hidden="true">
        <circle cx="38" cy="38" r="36" fill="rgba(0,0,0,.35)" stroke="#fff" stroke-width="3"/>
        <path d="M30 24l24 14-24 14z" fill="#fff"/>
      </svg>
    </div>
    <h2 class="exercise-title">Lorem ipsum dolor sit amet</h2>
    <div class="tags">
      <span class="tag tag-flexibility">Flexibility</span>
      <span class="tag tag-leg">Leg</span>
      <span class="tag tag-pain">Pain Relief</span>
    </div>
    <p class="exercise-description">Lorem ipsum dolor sit amet, consectetur adipiscing elit. Etiam vitae eros efficitur, finibus sapien et, porta libero. Integer facilisis massa dolor. Vivamus tempor enim sit amet lectus vehicula, eget luctus quam dignissim. Sed eu accumsan lacus. Nam et ullamcorper magna. Integer id diam varius arcu vestibulum porttitor.</p>
    <p class="meta meta-time"><span class="meta-label">Time:</span> 5:32 min</p>
    <p class="meta meta-level"><span class="meta-label">Level:</span> Moderate</p>
  </section>

  <section class="card timer-card">
    <h3 class="timer-label">Timer</h3>
    <span class="timer-note">Lorem ipsum</span>
    <div class="progress-track"><div class="progress-fill">18%...</div></div>
  </section>

  <div class="start-button">START</div>
</main>
</body>
</html>
```